The Korvane LLC Asset Classes

I'm looking for for two designs here to go into powerpoint and potentially as a standalone PDF. My company does wealth management.
Graphic Image #1
I break down the investment world into 4 broad categories
-Preservation
-Capital Markets
-Real Estate
-Alternatives
In each broad category, there are subcategories:
Preservation: cash, checking/savings accounts, money market accounts, CD's, and fixed annuities.
Capital Markets: Publicly traded stocks and bonds
Real Estate: single-family residence, retail, industrial, multifamily, and office
Alternatives: private equity, private credit, cryptocurrency, asset-backed loans, tax liens, oil & gas, litigation finance, and royalties
Graphic 2: Please see the bottom f page 1 of the Tessolin Decks PDF.
Just like in graphic one, you have 4 categories of the Capital Markets and their respective subcategories
Category 1: Domestic Stocks: Subcategories are Large, mid, and small size companies
Category 2: International Stocks: Subcategories are Large, Mid/Small and by region - Developed and Emerging
Category 3: Fixed Income: You have subcategories like corporate, municipal, government, domestic, international
Category 4: Alternatives: The subcategories are metals and real estate
---------------------
I'm looking to create a graphic (either pie chart, or a circle broken into parts or some other clever way to illustrate this) to clearly illustrate both of these universes in a clean, professional, slick manner.
Target Market(s)
Investors
Colors
Designer to choose colors to be used in the design.
Requirements
Must have
- Clean
- professional
- Easy to read
- Creative
- Visually appealling
Nice to have
- I have attached my logo and some marketing materials so you can get a feel of what I am doing. Maybe you can clean this up too!

```html
<!DOCTYPE html>
<html lang="en">
<head>
<meta charset="utf-8">
<title>Capital Markets – Korvane LLC</title>
<link href="https://fonts.googleapis.com/css2?family=Fira+Sans:wght@400;500;600&family=Kanit:wght@600&display=swap" rel="stylesheet">
<style>
  :root {
    --page-bg: #c4c5c7;
    --slide-bg: #ffffff;
    --title-orange: #f08b45;
    --brand-navy: #17628a;
    --body-grey: #4f4f52;
    --domestic-green: #5fb55d;
    --international-blue: #0769ad;
    --fixed-brown: #a97b50;
    --alternatives-grey: #a3a3a3;
    --ring-orange: #ec9a3c;
  }
  html, body {
    margin: 0;
    width: 1200px;
    height: 1000px;
    overflow: hidden;
    background: var(--page-bg);
  }
  .slide {
    position: absolute;
    left: 0;
    top: 50px;
    width: 1200px;
    height: 900px;
    background: var(--slide-bg);
    font-family: "Fira Sans", sans-serif;
  }
  .slide-title {
    position: absolute;
    left: 48px;
    top: 46px;
    margin: 0;
    font-weight: 400;
    font-size: 42px;
    color: var(--title-orange);
    letter-spacing: 0.3px;
  }
  .brand-mark {
    position: absolute;
    right: 50px;
    top: 58px;
    display: flex;
    align-items: center;
    gap: 10px;
    font-family: "Fira Sans", sans-serif;
    font-weight: 600;
    font-size: 30px;
    color: var(--brand-navy);
  }
  .brand-dot {
    width: 22px;
    height: 22px;
    border-radius: 50%;
    background: var(--brand-navy);
  }
  .market-wheel {
    position: absolute;
    left: 0;
    top: 0;
    width: 1200px;
    height: 900px;
  }
  .segment-label {
    font-family: "Kanit", sans-serif;
    font-weight: 600;
    font-size: 23px;
    fill: #ffffff;
    text-anchor: middle;
  }
  .callout-text {
    font-family: "Fira Sans", sans-serif;
    font-weight: 500;
    font-size: 17px;
    fill: var(--body-grey);
  }
  .hub-name {
    font-family: "Fira Sans", sans-serif;
    font-weight: 600;
    font-size: 21px;
    fill: var(--brand-navy);
    text-anchor: middle;
  }
</style>
</head>
<body>
<main class="slide">
  <h1 class="slide-title">Capital Markets</h1>
  <div class="brand-mark"><span class="brand-dot"></span>Korvane LLC</div>

  <svg class="market-wheel" viewBox="0 0 1200 900" role="img" aria-label="Capital markets wheel: domestic stocks, international stocks, fixed income, alternatives">
    <defs>
      <filter id="segment-shadow" x="-20%" y="-20%" width="140%" height="140%">
        <feDropShadow dx="-6" dy="8" stdDeviation="10" flood-color="#000" flood-opacity="0.22"/>
      </filter>
      <filter id="hub-shadow" x="-30%" y="-30%" width="160%" height="160%">
        <feDropShadow dx="4" dy="6" stdDeviation="8" flood-color="#000" flood-opacity="0.3"/>
      </filter>
      <linearGradient id="hub-fill" x1="0" y1="0" x2="0" y2="1">
        <stop offset="0" stop-color="#ffffff"/>
        <stop offset="1" stop-color="#d9d9db"/>
      </linearGradient>
      <linearGradient id="ring-stroke" x1="0" y1="0" x2="1" y2="1">
        <stop offset="0" stop-color="#fbe7d3"/>
        <stop offset="1" stop-color="var(--ring-orange)"/>
      </linearGradient>
    </defs>

    <!-- callout lines -->
    <g class="callouts" fill="none" stroke-width="1.2">
      <polyline points="207,249 398,249" stroke="var(--domestic-green)"/>
      <polyline points="747,216 978,216 978,246" stroke="var(--international-blue)"/>
      <polyline points="364,643 212,643 212,673" stroke="#9a9a9a"/>
      <polyline points="825,676 947,676" stroke="var(--fixed-brown)"/>
    </g>
    <circle cx="207" cy="249" r="4" fill="var(--domestic-green)"/>
    <circle cx="978" cy="246" r="4" fill="var(--international-blue)"/>
    <circle cx="212" cy="673" r="4" fill="#9a9a9a"/>
    <circle cx="947" cy="676" r="4" fill="var(--fixed-brown)"/>

    <!-- segments -->
    <g class="segments" filter="url(#segment-shadow)">
      <path class="segment-alternatives" d="M614,488 L614,781 A293,293 0 0 1 321,488 Z" fill="var(--alternatives-grey)"/>
      <path class="segment-fixed-income" d="M614,488 L894,488 A280,280 0 0 1 614,768 Z" fill="var(--fixed-brown)"/>
      <path class="segment-international" d="M614,488 L614,183 A305,305 0 0 1 919,488 Z" fill="var(--international-blue)"/>
      <path class="segment-domestic" d="M614,488 L290,488 A324,324 0 0 1 614,164 Z" fill="var(--domestic-green)"/>
    </g>

    <text class="segment-label" x="453" y="338">Domestic<tspan x="453" dy="27">Stocks</tspan></text>
    <text class="segment-label" x="745" y="338">International<tspan x="745" dy="27">Stocks</tspan></text>
    <text class="segment-label" x="484" y="638">Alternatives</text>
    <text class="segment-label" x="743" y="625">Fixed<tspan x="743" dy="27">Income</tspan></text>

    <!-- hub -->
    <circle cx="614" cy="488" r="118" fill="url(#hub-fill)" filter="url(#hub-shadow)"/>
    <circle cx="614" cy="488" r="104" fill="none" stroke="url(#ring-stroke)" stroke-width="3"/>
    <text class="hub-name" x="614" y="495">Korvane LLC</text>

    <!-- callout text -->
    <text class="callout-text" x="169" y="276">Large, mid,<tspan x="169" dy="23.5">and small</tspan><tspan x="169" dy="23.5">companies</tspan></text>
    <text class="callout-text" x="915" y="267">• Large, mid/small<tspan x="915" dy="23.5">• Developed and</tspan><tspan x="930" dy="23.5">Emerging</tspan></text>
    <text class="callout-text" x="169" y="714">• Metals<tspan x="169" dy="23.5">• Real Estate</tspan></text>
    <text class="callout-text" x="897" y="714">• Corporate<tspan x="897" dy="23.5">• Municipal</tspan><tspan x="897" dy="23.5">• Government</tspan><tspan x="897" dy="23.5">• Domestic</tspan><tspan x="897" dy="23.5">• International</tspan></text>
  </svg>
</main>
</body>
</html>
```